Modern & Simple Essential Oils Label

Company Name: Meadowlark Essentials

What we sell: Aromatherapy products, pure therapeutic essential oils.

Design need:
We are looking for a creative and youthful design for the labels used on small essentials oils.

I have two sizes of bottles that I use for essential oils a 5ml bottle and a 15ml bottle. They are dark Amber color glass with black lids. I like the clear labels or mayble a dark brown background. With white or clear lettering with punch of color too! Each oil type is represented by different color. (lavender- purple, lemon - yellow). The label will be the same for all the oils in the two sizes with only a different oil name & coordinating color.
5ml label size should be: 1 " x 2.625"
15ml label size should be: 1.5" x 3.5"

I have some labels that I have had another designer start on, but they aren't quite what I want and missing that something (alot!).. I don't know what. Interest maybe? Lack of design? I dunno.. they are attached. Maybe it's the logo? I don't know! But its gotta change! When I cut out a proof and put a sample on the bottle as I look straight on at the label all I see is a big dot, no logo.. nothing interesting.
Updates

Project Deadline Extended
Reason: Hi! Id like to extend this deadline. Ive been unavailable for a few days due to an illness and Im so far behind! Im feeling MUCH better and looking forward to getting caught up and move with the project. Im not sure how this works, but I attached a list of the oils that we currently have available. And in the list is the idea for the color schemes for the oils. The basic idea is for it to have a wide array of colors, so using different shades of greens, yellows, oranges and so on. So that its like a rainbow. We are not set of that particular color for that particular oil. It was just a idea list of possible colors for oils. Thanks so much!

Target Market(s)

Metro & Modern people. Interested in healthy organic living, Mostly women (some men) 20-45 who are interested in holistic healing.

Industry/Entity Type

It Company

Requirements
Must have
• A reputable look. Clean, organic, crisp, zen or spa-like feel. Modern, youthful appealing label design. Approachable and interesting, not intimidating so that I don't turn away people who are new or not familiar with how to use essential oils.
Should not have
• do NOT want the look to be anywhere close to medicinal, witchy, crafty, hippie, mystical, overly earthy, magical, or voodoo. Do not want it to look like something out of a grandmothers medicine cabinet.

```html
<!DOCTYPE html>
<html lang="en">
<head>
<meta charset="utf-8">
<title>Meadowlark Essentials – Cassia 15 ml Label</title>
<link rel="stylesheet" href="https://fonts.googleapis.com/css2?family=Roboto:wght@400;700&family=Montserrat:ital,wght@0,300;1,600&family=Damion&display=swap">
<style>
  :root {
    --paper: #ffffff;
    --label-grey: #eeeceb;
    --stripe-field: #ecebea;
    --bronze: #8d6635;
    --ink-grey: #8a8a8a;
    --cream: #f3e8d6;
    --cut-line: #555555;
  }
  html, body {
    margin: 0;
    padding: 0;
    overflow: hidden;
    background: var(--paper);
  }
  .canvas {
    position: relative;
    width: 1200px;
    height: 591px;
    overflow: hidden;
    background: var(--paper);
  }
  .cut-mark {
    position: absolute;
    left: 600px;
    width: 1px;
    height: 26px;
    background: var(--cut-line);
  }
  .cut-mark--top { top: 44px; }
  .cut-mark--bottom { top: 520px; }

  /* back panel: info text runs bottom to top */
  .back-panel {
    position: absolute;
    left: 75px;
    top: 68px;
    width: 525px;
    height: 453px;
    background: var(--label-grey);
  }
  .back-panel__rotor {
    position: absolute;
    left: 0;
    top: 0;
    width: 453px;
    height: 525px;
    transform-origin: 0 0;
    transform: translate(0, 453px) rotate(-90deg);
    font-family: "Roboto", Arial, sans-serif;
    color: var(--ink-grey);
    font-size: 18.5px;
    line-height: 22.5px;
    letter-spacing: -0.2px;
  }
  .facts-box {
    position: absolute;
    left: 16px;
    top: 15px;
    width: 417px;
    height: 162px;
    box-sizing: border-box;
    border: 3px solid var(--bronze);
    border-bottom: none;
  }
  .facts-box__title {
    position: absolute;
    left: 12px;
    top: 10px;
    margin: 0;
    font-size: 22px;
    font-weight: 700;
    line-height: 26px;
  }
  .facts-box__list {
    position: absolute;
    left: 12px;
    top: 39px;
    margin: 0;
    padding: 0;
    list-style: none;
    font-size: 18px;
    line-height: 22px;
  }
  .facts-box__band {
    position: absolute;
    left: -3px;
    right: -3px;
    bottom: 0;
    height: 32px;
    background: var(--bronze);
    color: var(--cream);
    font-size: 18.5px;
    line-height: 32px;
    padding-left: 15px;
  }
  .back-copy {
    position: absolute;
    left: 16px;
    margin: 0;
    width: 432px;
  }
  .back-copy--company { top: 193px; }
  .back-copy--usage { top: 258px; }
  .back-copy--caution { top: 347px; }
  .back-copy strong { font-weight: 700; }

  /* front panel */
  .front-panel {
    position: absolute;
    left: 600px;
    top: 68px;
    width: 525px;
    height: 453px;
    background: var(--label-grey);
  }
  .front-panel__texture {
    position: absolute;
    inset: 0;
    background: var(--stripe-field);
  }
  .botanical-name {
    position: absolute;
    left: 335px;
    top: 46px;
    margin: 0;
    font-family: "Montserrat", "Century Gothic", sans-serif;
    font-style: italic;
    font-weight: 600;
    font-size: 20.5px;
    line-height: 29px;
    color: var(--ink-grey);
    text-transform: uppercase;
  }
  .oil-name {
    position: absolute;
    left: 22px;
    top: 128px;
    margin: 0;
    font-family: "Damion", cursive;
    font-weight: 400;
    font-size: 158px;
    line-height: 200px;
    color: var(--bronze);
  }
  .volume {
    position: absolute;
    left: 20px;
    top: 372px;
    width: 32px;
    height: 78px;
    margin: 0;
    writing-mode: vertical-rl;
    transform: rotate(180deg);
    font-family: "Roboto", Arial, sans-serif;
    font-weight: 700;
    font-size: 25px;
    line-height: 32px;
    text-align: center;
    color: var(--bronze);
  }
  .brand-band {
    position: absolute;
    left: 57px;
    top: 372px;
    right: 0;
    height: 79px;
    background: var(--bronze);
    display: flex;
    align-items: center;
    justify-content: center;
  }
  .brand-band__name {
    font-family: "Montserrat", "Century Gothic", sans-serif;
    font-weight: 300;
    font-size: 31px;
    color: var(--cream);
  }
</style>
</head>
<body>
<div class="canvas">
  <div class="cut-mark cut-mark--top"></div>
  <div class="cut-mark cut-mark--bottom"></div>

  <section class="back-panel">
    <div class="back-panel__rotor">
      <div class="facts-box">
        <h2 class="facts-box__title">Supplemental Facts</h2>
        <ul class="facts-box__list">
          <li>Serving Size: 1 drop</li>
          <li>Servings Per Container: About 250</li>
          <li>Oil: Rosmarinus Officinalis</li>
        </ul>
        <div class="facts-box__band">100% Pure Therapeutic Grade</div>
      </div>
      <p class="back-copy back-copy--company">Meadowlark Essentials<br>P.O. Box 407, Fairhaven, UT 84120</p>
      <p class="back-copy back-copy--usage">For aromatic, topical use. 100% pure therapeutic-grade essential oil. Dilute with a carrier oil before using.</p>
      <p class="back-copy back-copy--caution"><strong>CAUTION:</strong> For External Use Only. Not for Ingestion. Keep away from eyes and mucous membranes. May cause skin sensitivity. If pregnant consult physician before use. Keep out of reach of children. Keep away from flame.</p>
    </div>
  </section>

  <section class="front-panel">
    <div class="front-panel__texture" role="img" aria-label="Fine vertical pinstripe texture in light grey"></div>
    <p class="botanical-name">Cinnamomum<br>Cassia<br>100% Pure<br>Essential Oil</p>
    <h1 class="oil-name">Cassia</h1>
    <p class="volume">15 ml</p>
    <div class="brand-band">
      <span class="brand-band__name">meadowlark essentials</span>
    </div>
  </section>
</div>
</body>
</html>
```